QSR ebook cover for modern romance book

I am looking for an ebook cover in the correct size and format for Quillrise Self Releasing, which will look good in thumbnail and at full size.
My book is a happily ever after romance with a kinky theme. It is set in the modern day in an Oxford/Cambridge-style university town in the UK. It tells the story of a couple who are reunited eight years after she broke his heart because she could not abandon her vocation to follow him to another country, and how they come to fall in love again despite the obstacles.
The book is already published with a current cover I designed myself: https://www.brindlemart.co.uk/gp/product/Q417X58TLM/ I used a stock photo which I purchased and which you could reuse if you wanted (I have the original file which I can share; lower resolution image attached below), but I am very open to other ideas and images.
I like my current cover but I feel it could be improved so that it has more impact in a crowded marketplace, and so that it looks more professional and high-end.
I deliberately avoided copying the style of many modern and erotic romances which have explicit, bold covers (such as this https://www.brindlemart.co.uk/Hold-Us-Close-Lone-Amour-ebook/dp/Q35T2WR81K/ or https://www.brindlemart.co.uk/gp/product/Q52N8HX7PF or https://www.brindlemart.co.uk/Lit-Within-Emberline-Nora-Lund-ebook/dp/Q71403J2VC/ ) as I feel those styles of cover would misrepresent the tone and content of my book.
I do not want a picture of a topless man or a stock picture of a couple on my cover. I would like to hint at the kinky theme, but using a visual style which is more literary/romantic than erotic.
Ideally I would like room to add a short line of text to the cover in addition to the title and author, but this is not essential.
I am very happy to provide more information or answer any questions.

```html
<!DOCTYPE html>
<html lang="en">
<head>
<meta charset="utf-8">
<title>Follow Me — Clara Vane</title>
<link rel="stylesheet" href="https://fonts.googleapis.com/css2?family=Pinyon+Script&family=Playfair+Display:ital@1&display=swap">
<style>
  :root {
    --backdrop: #0e1012;
    --ink-cream: #ecead4;
    --ink-shade: rgba(60, 10, 40, 0.55);
    --tone-copper: #7a3d22;
    --tone-rose: #c3195c;
    --tone-hotpink: #ff3a7e;
    --tone-plum: #4d1d72;
    --tone-night: #180910;
  }
  html, body {
    margin: 0;
    width: 1200px;
    height: 1200px;
    overflow: hidden;
    background: var(--backdrop);
  }
  .cover {
    position: absolute;
    left: 291px;
    top: 161px;
    width: 586px;
    height: 878px;
    overflow: hidden;
    box-shadow: 0 20px 50px rgba(0, 0, 0, 0.6);
  }
  .cover-art {
    position: absolute;
    inset: 0;
    background:
      radial-gradient(ellipse 40% 30% at 100% 18%, var(--tone-hotpink), transparent 70%),
      radial-gradient(ellipse 35% 35% at 95% 85%, var(--tone-plum), transparent 75%),
      radial-gradient(ellipse 50% 22% at 35% 8%, #a35a3a, transparent 70%),
      radial-gradient(ellipse 55% 45% at 60% 45%, var(--tone-rose), transparent 75%),
      linear-gradient(160deg, var(--tone-copper) 0%, #5a1a2e 35%, #6e1240 55%, var(--tone-night) 80%, #2a0f3a 100%);
  }
  .title {
    position: absolute;
    margin: 0;
    font-family: "Pinyon Script", cursive;
    font-weight: 400;
    color: var(--ink-cream);
    line-height: 1;
    white-space: nowrap;
    text-shadow: 2px 3px 3px var(--ink-shade), -1px -1px 0 rgba(255, 255, 255, 0.25);
  }
  .title-follow {
    left: -20px;
    top: 150px;
    font-size: 250px;
    letter-spacing: -12px;
  }
  .title-me {
    left: 160px;
    top: 330px;
    font-size: 250px;
    letter-spacing: -10px;
  }
  .author {
    position: absolute;
    left: 60px;
    top: 432px;
    margin: 0;
    font-family: "Playfair Display", serif;
    font-style: italic;
    font-size: 28px;
    line-height: 33px;
    color: var(--ink-cream);
  }
</style>
</head>
<body>
  <main class="cover">
    <div class="cover-art" role="img" aria-label="Close-up of a woman's face veiled by strands of hair, lit in copper, pink and violet"></div>
    <h1 class="title-wrap">
      <span class="title title-follow">follow</span>
      <span class="title title-me">me</span>
    </h1>
    <p class="author">Clara<br>Vane</p>
  </main>
</body>
</html>
```